Business Card Design

New business card design

Target Market(s)

Residential & Commercial Property Managers

Industry/Entity Type

Plumbing Services

Contact Information for Business Card

Name - Rowan Keddle, title - Director, Phone Number - 0431 286 517, email - rowan@tbk-plumbing.com.au, Company ABN - 73 215 904 386,

Font styles to use
Sans Serif

Colors
0054AA
0677BA
7BADD7
CADEEF
E8F1F8

```html
<!DOCTYPE html>
<html lang="en">
<head>
<meta charset="utf-8">
<title>TBK Plumbing Services – Business Card</title>
<link href="https://fonts.googleapis.com/css2?family=Montserrat:wght@400;500;700&display=swap" rel="stylesheet">
<style>
  :root {
    --backdrop: #e6e4e5;
    --card: #ffffff;
    --ink: #1f2a33;
    --accent: #2fa3dc;
    --rule: #1f2a33;
  }
  * { margin: 0; padding: 0; box-sizing: border-box; }
  html, body {
    width: 1200px; height: 1108px; overflow: hidden;
    background: var(--backdrop);
    font-family: "Montserrat", sans-serif;
    color: var(--ink);
  }
  .canvas { position: relative; width: 1200px; height: 1108px; }
  .card {
    position: absolute;
    background: var(--card);
  }
  .card--front { left: 240px; top: 62px; width: 750px; height: 453px; }
  .card--back { left: 239px; top: 589px; width: 751px; height: 441px; }

  .brand {
    position: absolute;
    display: flex; align-items: center;
    white-space: nowrap;
  }
  .brand__dot {
    border-radius: 50%;
    background: var(--accent);
    flex: none;
  }
  .brand__name {
    font-weight: 500;
    color: var(--ink);
    letter-spacing: 0.01em;
  }
  .card--front .brand { left: 68px; top: 221px; gap: 10px; }
  .card--front .brand__dot { width: 16px; height: 16px; }
  .card--front .brand__name { font-size: 21px; }

  .card--back .brand { left: 0; right: 0; top: 190px; justify-content: center; gap: 18px; }
  .card--back .brand__dot { width: 34px; height: 34px; }
  .card--back .brand__name { font-size: 46px; }

  .divider {
    position: absolute; left: 372px; top: 150px;
    width: 2px; height: 186px; background: var(--rule);
  }
  .contact { position: absolute; left: 393px; top: 146px; }
  .contact__name { font-size: 27px; font-weight: 700; line-height: 1.2; }
  .contact__title { font-size: 16px; font-weight: 400; margin-top: 0; }
  .contact__list { list-style: none; margin-top: 16px; }
  .contact__item {
    display: flex; align-items: center; gap: 10px;
    font-size: 16px; height: 31px;
  }
  .contact__item svg { width: 17px; height: 17px; fill: var(--ink); flex: none; }
  .contact__abn { font-size: 16px; margin-top: 0; }
  .contact__abn strong { font-weight: 700; }
</style>
</head>
<body>
<main class="canvas">
  <section class="card card--front">
    <div class="brand">
      <span class="brand__dot"></span>
      <span class="brand__name">TBK Plumbing Services</span>
    </div>
    <div class="divider"></div>
    <div class="contact">
      <h1 class="contact__name">Rowan Keddle</h1>
      <p class="contact__title">Director</p>
      <ul class="contact__list">
        <li class="contact__item">
          <svg viewBox="0 0 24 24" aria-hidden="true"><path d="M6.6 10.8a15 15 0 0 0 6.6 6.6l2.2-2.2a1 1 0 0 1 1-.25 11.4 11.4 0 0 0 3.6.57 1 1 0 0 1 1 1V20a1 1 0 0 1-1 1A17 17 0 0 1 3 4a1 1 0 0 1 1-1h3.5a1 1 0 0 1 1 1c0 1.25.2 2.45.57 3.57a1 1 0 0 1-.25 1z"/></svg>
          <span>0431 286 517</span>
        </li>
        <li class="contact__item">
          <svg viewBox="0 0 24 24" aria-hidden="true"><path d="M3 6h18v12H3z" fill="none"/><path d="M3 6h18v1.5l-9 5.5-9-5.5zM3 9.3l9 5.5 9-5.5V18H3z"/></svg>
          <span>rowan@tbk-plumbing.com.au</span>
        </li>
        <li class="contact__item">
          <svg viewBox="0 0 24 24" aria-hidden="true"><path d="M12 2a10 10 0 1 0 0 20 10 10 0 0 0 0-20zm0 2a8 8 0 0 1 6.9 4H15l-1 2-2-1-2 2 1 2-1 2 1 3-1 1.9A8 8 0 0 1 5 8.5L7 10l2 3 1-3-2-2 1-3z"/></svg>
          <span>www.tbk-plumbing.com.au</span>
        </li>
      </ul>
      <p class="contact__abn"><strong>ABN</strong> - 73 215 904 386,</p>
    </div>
  </section>

  <section class="card card--back">
    <div class="brand">
      <span class="brand__dot"></span>
      <span class="brand__name">TBK Plumbing Services</span>
    </div>
  </section>
</main>
</body>
</html>
```